Copper Moth Bar & Grill Takeout Menu

Please create a takeout menu using the attached dine-in menu.
Take out menu size: Tri-Fold 11x17

Industry/Entity Type

Bar & Grill (Restaurant)

Colors

Designer to choose colors to be used in the design.

Requirements
Must have
• Phone number and website. "Order Online" "Order for Delivery"
Nice to have
• Area on the back of the menu to feature happy hour specials.

```html
<!DOCTYPE html>
<html lang="en">
<head>
<meta charset="utf-8">
<title>Copper Moth Bar &amp; Grill — Takeout Menu</title>
<link href="https://fonts.googleapis.com/css2?family=Almendra:ital,wght@0,400;0,700;1,400&family=Almendra+SC&family=Alfa+Slab+One&family=Poppins:wght@400;500;600;700&display=swap" rel="stylesheet">
<style>
:root{
  --teal:#4fdfe4;
  --yellow:#fdd84f;
  --paper:#ebebeb;
  --ink:#1d1d1d;
  --muted:#555;
  --line:#5b5b5b;
  --stage:#f4f4f4;
  --art:#c9c9c9;
}
*{margin:0;padding:0;box-sizing:border-box}
html,body{width:1200px;height:2599px;overflow:hidden}
body{background:var(--stage);font-family:'Poppins',sans-serif;color:var(--ink);position:relative}
.spread{position:absolute;left:85px;width:1020px;height:665px;background:var(--paper);box-shadow:0 6px 18px rgba(0,0,0,.18);overflow:hidden}
.spread--outside{top:985px}
.spread--inside{top:1782px}
.panel{position:absolute;top:12px;bottom:14px;padding:30px 18px 10px}
.framed{border:3px double var(--line)}
.p-left{left:10px;width:320px}
.p-mid{left:350px;width:315px;padding:20px 10px 6px}
.p-right{left:672px;width:336px}
.ribbon{height:32px;display:flex;align-items:center;justify-content:center;font-family:'Almendra SC',serif;font-size:15px;letter-spacing:.5px;clip-path:polygon(0 0,100% 0,95% 50%,100% 100%,0 100%,5% 50%);margin:0 auto 14px;text-align:center;line-height:1;white-space:nowrap}
.ribbon--teal{background:var(--teal)}
.ribbon--yellow{background:var(--yellow)}
.ribbon--script{font-family:'Almendra',serif;font-style:italic;font-size:13px;height:auto;padding:6px 24px;line-height:1.3}
.group-title{font-family:'Almendra SC',serif;font-size:14.5px;margin:8px 0 3px;letter-spacing:.3px}
.row{display:flex;justify-content:space-between;align-items:center;font-size:10.3px;line-height:1.55;gap:8px}
.price{background:var(--teal);color:#fff;font-weight:700;font-size:10px;min-width:20px;text-align:center;line-height:14px;padding:0 3px}
.note{font-size:6.6px;color:var(--muted);line-height:1.35;margin:2px 0 4px}
.item{margin-bottom:8px}
.p-mid .item{margin-bottom:4px}
.p-mid .note{margin:1px 0 2px}
.item .row{font-weight:600;font-size:10px}
.cupbowl{font-size:9px;font-weight:600;text-align:right;line-height:1.2}
.art{background:var(--art);border-radius:6px}
.center{text-align:center}
.list{font-size:10px;line-height:1.3;text-align:center;margin-bottom:12px}

/* happy hour */
.happy{position:relative;display:flex;align-items:center;justify-content:space-between;margin:8px 4px 4px 2px}
.happy-word{position:relative;font-family:'Alfa Slab One',serif;font-size:52px;line-height:1;letter-spacing:1px}
.happy-word span{position:absolute;left:48px;top:12px;font-family:'Almendra SC',serif;font-size:22px;color:var(--teal);-webkit-text-stroke:.5px #333}
.happy-days{font-size:26px;line-height:1.18;text-align:center;border-top:1px solid #bbb;padding-top:5px}
.phone{display:flex;align-items:center;justify-content:center;gap:8px;background:var(--yellow);width:245px;margin:8px auto 4px;padding:3px 10px;font-family:'Alfa Slab One',serif;font-size:22px;white-space:nowrap;line-height:1.2}
.web{font-size:15px;font-weight:600;letter-spacing:1.5px;text-align:center;white-space:nowrap}

/* cover */
.cover-band{position:absolute;left:76px;top:0;width:183px;height:425px;background:var(--teal)}
.cover-mark{position:absolute;left:92px;top:30px;font-family:'Almendra',serif;font-size:24px;line-height:1.25;color:var(--ink)}
.cover-art{position:absolute;left:28px;top:150px;width:282px;height:280px}
.cover-name{position:absolute;left:0;right:0;top:448px;font-family:'Almendra SC',serif;font-weight:700;font-size:34px;line-height:1;text-align:center}
.cover-order{position:absolute;left:0;right:0;top:538px;display:flex;justify-content:center;gap:14px;font-family:'Almendra',serif;font-size:16px}
.cover-order span{display:flex;align-items:center;gap:6px}
.dot{width:9px;height:9px;border-radius:50%;background:var(--teal);display:inline-block}
.cover-web{position:absolute;left:0;right:0;top:582px;font-size:15px;letter-spacing:1.5px;text-align:center;font-weight:500}

/* burgers */
.prices3{display:flex;gap:14px;font-weight:600;font-size:10px}
.prices3 span{width:28px;text-align:right}
.sides{border:3px double var(--line);padding:12px 16px 6px;margin:4px 10px 14px}
.legend{display:flex;gap:10px;align-items:center;font-size:6px;margin-top:8px}
.tag{background:var(--teal);padding:1px 6px}
</style>
</head>
<body>

<!-- OUTSIDE -->
<section class="spread spread--outside">
  <div class="panel p-left framed">
    <div class="ribbon ribbon--teal" style="width:250px">STARTERS</div>
    <div class="group-title">TORTILLA CHIPS</div>
    <div class="row">with House-made Salsa Verde<span class="price">7</span></div>
    <div class="row">with House-made Fire Roasted Salsa<span class="price">7</span></div>
    <div class="row">with Guacamole &amp; Pico De Gallo<span class="price">8</span></div>
    <div class="row">with Queso<span class="price">8</span></div>
    <div class="row">with Chili con Queso<span class="price">9</span></div>
    <div class="group-title">WINGS</div>
    <div class="row"><b>8 pieces</b><span class="price">14</span></div>
    <p class="note">Flash-fried to a crispy golden brown and tossed in your choice of sauce. Choose from our Signature Hot, or Mild Sauce, or BBQ. Your choice of ranch or blue cheese.</p>
    <div class="group-title">QUESADILLAS</div>
    <div class="row">Cheddar and Monterey Jack Cheese<span class="price">12</span></div>
    <div class="row">Pulled Marinated Chicken &amp; Cheese<span class="price">16</span></div>
    <div class="row">Fire Roasted Vegetables &amp; Cheese<span class="price">14</span></div>
    <div class="row">Garlic Roasted Shrimp &amp; Cheese<span class="price">16</span></div>
    <p class="note">All quesadillas are stuffed with roasted red peppers, black beans and your choice below. Served with guacamole, pico de gallo, and chipotle crema on the side.</p>
    <div class="group-title">CLAW-FULL NACHOS</div>
    <div class="row">Copper Moth Chili Nachos<span class="price">14</span></div>
    <div class="row">Pulled Chicken Nachos<span class="price">16</span></div>
    <div class="row">Garlic Roasted Shrimp<span class="price">16</span></div>
    <div class="row">Fire Roasted Vegetables Nachos<span class="price">14</span></div>
    <p class="note">Tortilla chips, melted white queso, Cheddar and Monterey Jack cheeses, pico de gallo, guacamole, chipotle sour cream, jalapenos, black beans, &amp; green onions</p>
    <div class="group-title">FRENCH FRIES</div>
    <p class="note">Served with our house made Garlic Aioli and Spicy Ketchup.</p>
    <div class="row">Fries Only<span class="price">7</span></div>
    <div class="row">Sweet Potato Fries<span class="price">7</span></div>
    <div class="row">Cheddar-Jack Cheese Fries<span class="price">8</span></div>
    <div class="row">Cheddar-Jack Cheese, Bacon Fries<span class="price">9</span></div>
    <div class="row">Chili Cheese Fries<span class="price">10</span></div>
    <p class="note">Topped with Copper Moth Chili, cheddar jack cheese and served with chipotle crema on the side.</p>
  </div>

  <div class="panel p-mid">
    <div class="ribbon ribbon--yellow" style="width:200px;margin-bottom:10px">SALADS</div>
    <div class="item"><div class="row">Combo Cat<span class="price">11</span></div><p class="note">Enjoy a side House and a cup of any soup.</p></div>
    <div class="item"><div class="row">Cat House Salad<span class="price">11</span></div><p class="note">Spring lettuce mix, fresh red peppers, onion, cherry tomatoes, cucumber, and croutons. Served with Red Wine Vinaigrette.</p></div>
    <div class="item"><div class="row">Grilled Chicken Salad<span class="price">15</span></div><p class="note">Spring lettuce mix, grilled chicken breast, bacon, fresh red peppers, onions, tomatoes, cucumber and feta cheese. Served with Red Wine Vinaigrette</p></div>
    <div class="item"><div class="row">Grilled Shrimp Salad<span class="price">16</span></div><p class="note">Spring lettuce mix, garlic Roasted Shrimp, roasted corn, pico de gallo fresh avocado, Served with Lemon Champagne Vinaigrette</p></div>
    <div class="item"><div class="row">Goat Cheese Salad<span class="price">16</span></div><p class="note">Spring lettuce mix, fried goat cheese, fresh red peppers, cranberries, white onions, and cherry tomatoes. Served with Lemon Champagne Vinaigrette.</p></div>
    <div class="item"><div class="row">The Skinny Cat<span class="price">14</span></div><p class="note">Spring lettuce mix, sliced apple, sun dried cranberries, roasted corn, cherry tomatoes, and feta cheese. Served with Balsamic Vinaigrette.</p></div>
    <div class="item"><div class="row">Small House Salad<span class="price">6</span></div></div>
    <div class="ribbon ribbon--teal ribbon--script" style="width:290px;margin:8px auto 6px">Grilled Chicken 5 | Garlic Roasted Shrimp 5<br>Fried Goat Cheese 4</div>
    <div class="happy">
      <div class="happy-word">HOUR<span>HAPPY</span></div>
      <div class="art" role="img" aria-label="Line drawing of a sitting cat" style="width:46px;height:50px"></div>
    </div>
    <div class="happy-days">EVERY FRIDAY FROM<br>8 TO 10 PM</div>
    <div class="phone">
      <svg width="22" height="22" viewBox="0 0 24 24" aria-hidden="true"><circle cx="12" cy="12" r="11" fill="#1e6fd9"/><path d="M8.2 6.5l1.8 2.6-1 1.3c.8 1.7 2 2.9 3.6 3.7l1.3-1 2.6 1.8-.8 2c-4.7-.3-8.6-4.2-8.9-8.9z" fill="#fff"/></svg>
      <span>555-014-2290</span>
    </div>
    <div class="web">www.coppermothgrill.com</div>
  </div>

  <div class="panel p-right framed">
    <div class="cover-band"></div>
    <div class="cover-mark">Copper Moth<br>Bar &amp; Grill</div>
    <div class="cover-art art" role="img" aria-label="Illustration of a black cat with a bow sitting on carved pumpkins"></div>
    <div class="cover-name">COPPER MOTH<br>BAR &amp; GRILL</div>
    <div class="cover-order"><span><i class="dot"></i>Order Online</span><span><i class="dot"></i>Order for Delivery</span></div>
    <div class="cover-web">www.coppermothgrill.com</div>
  </div>
</section>

<!-- INSIDE -->
<section class="spread spread--inside">
  <div class="panel p-left framed">
    <div class="ribbon ribbon--yellow" style="width:240px">SOUPS &amp; BOWLS</div>
    <div class="item"><div class="row">Copper Moth Chili<span class="cupbowl">Cup 6<br>Bowl 8</span></div><p class="note">Copper Moth Signature Chili with lean ground beef, black beans, and corn. Topped with cheddar cheese and green onion, served with tri-color tortilla chips.</p></div>
    <div class="item"><div class="row">Southwestern Sweet Potato Soup<span class="cupbowl">Cup 6<br>Bowl 8</span></div><p class="note">A delicious mix of sweet potatoes, corn, bell peppers, and black beans, this vegan soup delivers top flavor and quality with every bowl. Served with tri-color tortilla chips.</p></div>
    <div class="item"><div class="row">Ancient Grains Bowl<span class="price">12</span></div><p class="note">Quinoa, brown rice, kale and fresh spinach, with fire roasted portobello mushrooms, zucchini and red peppers. Topped with fresh avocado, and feta cheese. Served with Lemon Champagne Vinaigrette</p></div>
    <div class="ribbon ribbon--teal ribbon--script" style="width:290px">Grilled Chicken 5 | Garlic Roasted Shrimp 5</div>
    <div class="center" style="font-family:'Almendra',serif;font-style:italic;font-size:13px">Dressings</div>
    <div class="list" style="margin-bottom:10px">Balsamic Vinaigrette | Caesar<br>Red Wine Vinaigrette | Honey-Mustard | Lemon<br>Champagne Vinaigrette | Ranch | Blue Cheese</div>
    <div class="ribbon ribbon--yellow" style="width:200px">OTHER HANDHELDS</div>
    <p class="note">All served with Hand Cut Fries or Sweet Potato Fries. Premium sides available for an up charge + 2</p>
    <div class="item"><div class="row">Cat Club<span class="price">15</span></div><p class="note">Sliced whole wheat bread with roasted garlic aioli, grilled marinated chicken breast, provolone cheese bacon, lettuce and tomato.</p></div>
    <div class="item"><div class="row">Southwest Melt<span class="price">14</span></div><p class="note">Sliced whole wheat bread with roasted garlic aioli, 3 pepper colby jack, roasted red peppers and corn.</p></div>
    <div class="item"><div class="row">What's Gouda<span class="price">14</span></div><p class="note">Sliced whole wheat bread with roasted garlic aioli smoked gouda and provolone cheeses, roasted red peppers and portobello mushrooms.</p></div>
    <div class="item"><div class="row">Westover Melt<span class="price">14</span></div><p class="note">Sliced whole wheat bread with roasted garlic aioli, zucchini, portobello mushrooms, red peppers, with melted brie and provolone cheeses.</p></div>
    <div class="art" role="img" aria-label="Row of hand-drawn cartoon cats" style="position:absolute;left:40px;bottom:6px;width:220px;height:40px"></div>
  </div>

  <div class="panel p-mid" style="padding-top:28px">
    <div class="art" role="img" aria-label="Drawing of a cat peeking around the panel edge" style="position:absolute;left:-10px;top:20px;width:72px;height:78px"></div>
    <div class="ribbon ribbon--teal" style="width:230px">CHEESES</div>
    <div class="list">Vermont Cheddar | Smoked Gouda<br>3-Pepper Colby Jack<br>Monterey Jack | Swiss | Brie<br>Provolone | American</div>
    <div class="ribbon ribbon--yellow" style="width:230px">CONDIMENTS</div>
    <div class="list">Horseradish Aioli | Chipotle Crema<br>| Roasted Garlic Aioli | Citrus Aioli<br>Spicy Ketchup | Dijon Mustard |<br>Yellow Mustard | Mayo | Ketchup</div>
    <div class="ribbon ribbon--teal" style="width:240px">TOPPINGS</div>
    <div class="list">Bacon | Shrimp | Egg | Red Onion |<br>White Onion | Portobello Mushrooms |<br>Roasted Corn | Roasted Red Peppers<br>Guacamole | Pico De Gallo |<br>Fresh or Pickled Jalapeno</div>
    <div class="sides">
      <div class="center" style="font-family:'Almendra SC',serif;font-size:14px;margin-bottom:8px">SIDES</div>
      <div class="row" style="font-weight:600;font-size:9.5px;margin-bottom:8px">Potato Salad<span class="price">4</span></div>
      <div class="row" style="font-weight:600;font-size:9.5px;margin-bottom:8px">Fire Roasted Veggies<span class="price">6</span></div>
      <div class="row" style="font-weight:600;font-size:9.5px;margin-bottom:6px">Brown Rice, Quinoa, &amp; Kale Medley<span class="price">5</span></div>
    </div>
    <div style="position:relative">
      <div class="ribbon ribbon--yellow" style="width:230px;margin-bottom:6px">KIDS MENU</div>
      <div class="art" role="img" aria-label="Drawing of a lounging cat" style="position:absolute;right:8px;top:-10px;width:70px;height:40px"></div>
    </div>
    <p class="note center">All served with French Fries</p>
    <div class="row">Grilled Cheese<span class="price">8</span></div>
    <div class="row">Cheese Quesadilla<span class="price">8</span></div>
    <div class="row">Mac &amp; Cheese<span class="price">8</span></div>
    <div class="row">Chicken Tenders<span class="price">10</span></div>
  </div>

  <div class="panel p-right framed">
    <div class="ribbon ribbon--teal" style="width:240px;height:38px;font-size:13px;line-height:1;white-space:normal">GOURMET BURGERS<br>&amp; SANDWICHES</div>
    <p class="note" style="font-size:6.8px">Start with your style and then choose your protein. Our burgers are house made and cooked to your temperature. Our fresh grilled chicken breast is marinated in house and cooked to perfection. Keep it vegetarian by choosing a vegetarian style along with the Quinoa Lentil Burger. All are served on a potato bun with lettuce, tomato, onion, and your choice of hand cut fries or sweet potato fries. <b>Premium sides available for an up charge + $2</b></p>
    <div class="center" style="font-family:'Almendra SC',serif;font-size:11px;margin:6px 0 4px">GLUTEN-FREE BUN AVAILABLE UPON REQUEST | $2</div>
    <div class="row" style="justify-content:flex-end"><span class="prices3"><span>●</span><span>●</span><span>●</span></span></div>
    <div class="item"><div class="row">Calico Cat<span class="prices3"><span>15.00</span><span>14.00</span><span>13.00</span></span></div><p class="note">Roasted red peppers, red onions, brie cheese, and horseradish aioli.</p></div>
    <div class="item"><div class="row">Tiger Cat<span class="prices3"><span>15.00</span><span>14.00</span><span>13.00</span></span></div><p class="note">Cheddar, Monterey Jack, and Provolone</p></div>
    <div class="item"><div class="row">Cat Scratch Fever<span class="prices3"><span>15.50</span><span>14.50</span><span>13.50</span></span></div><p class="note">Guacamole, 3 pepper colby jack, pico de gallo, and chipotle mayo.</p></div>
    <div class="item"><div class="row">The Fat Cat<span class="prices3"><span>16.00</span><span>15.00</span><span>14.00</span></span></div><p class="note">Fried egg*, bacon, cheddar cheese, and garlic aioli.</p></div>
    <div class="item"><div class="row">Tabby Cat<span class="prices3"><span>16.50</span><span>15.50</span><span>14.50</span></span></div><p class="note">Melted brie cheese, sliced apple, and citrus aioli.</p></div>
    <div class="item"><div class="row">The Sphynx<span class="prices3"><span>16.50</span><span>15.50</span><span>14.50</span></span></div><p class="note">Portobello mushrooms, roasted red peppers, smoked gouda cheese, and roasted garlic aioli.</p></div>
    <div class="item"><div class="row">Maine Coon<span class="prices3"><span>16.50</span><span>15.50</span><span>14.50</span></span></div><p class="note">Grilled shrimp*, roasted corn, swiss cheese, and roasted garlic aioli.</p></div>
    <div class="item"><div class="row">Alley Cat<span class="prices3"><span>14.00</span><span>13.00</span><span>12.00</span></span></div><p class="note">Whats up your alley? Choose a cheese, condiment and one topping.</p></div>
    <div class="ribbon ribbon--yellow ribbon--script" style="width:290px;margin-bottom:6px;font-size:12px;padding:7px 16px">Additional Toppings $1 | Bacon, Egg, Shrimp - $2</div>
    <p class="note" style="width:190px">The consumption of raw or undercooked eggs, meat, poultry, seafood or shellfish may contribute to food borne illness, especially if you have a medical condition.</p>
    <div class="legend"><span>▾</span><span class="tag">Vegetarian</span><span>▾</span><span class="tag">Spicy</span></div>
    <div class="art" role="img" aria-label="Drawing of a family of cats" style="position:absolute;right:14px;bottom:12px;width:90px;height:76px"></div>
  </div>
</section>

</body>
</html>
```